Substance abuse awareness flyer for school age kids

I am needing a flyer for school-age kids. What if it were designed to look like an Quorby with someone texting and the text bubbles were some of the text below with emojis? Maybe a text chain between to friends:

Maybe the first text bubble says "I'm thinking about using drugs and alcohol"
the next bubble: "Just say no!" ( perhaps a stop sign emoji ?)

"Talk to your parents, your teachers at school, or your doctor about how drugs and alcohol can harm you"

another text bubble "did you know that alcohol and drugs could lead to..."
then include some of the info below (see links for more info).
Where ever you get info, it must be cited.

this needs to be English on one side and Spanish on the other side and needs to include the logo attached.

The effects of substance abuse
RMQ: https://www.rmqhealthnet.org/plwtrk/vesk/features/teen-substance-use.html
Affect growth and development, especially brain development. Not able to focus at school or be around friends. https://www.halvenstudy.org/sites/default/files/youthguide_2.pdf
Leads to risky behaviors and lack of impulse control (dangerous activities) https://www.halvenstudy.org/sites/default/files/youthguide_2.pdf
Contribute to health problems as an adult: heart disease, high blood pressure, and trouble sleeping.

Target Market(s)

school age kids 9-20

Requirements
Must have
• Print ready: 8.5x11

```html
<!DOCTYPE html>
<html lang="en">
<head>
<meta charset="utf-8">
<title>Substance Use Awareness Flyer</title>
<link rel="stylesheet" href="https://fonts.googleapis.com/css2?family=Montserrat:wght@500;600;700;800&display=swap">
<style>
  :root {
    --page-bg: #e9e7e4;
    --flyer-blue: #1479c5;
    --lime: #c3d92f;
    --sky: #72cde0;
    --maroon: #5a1f3a;
    --ink: #111a26;
    --label-blue: #1566c0;
    --bullet-blue: #1472c4;
    --white: #ffffff;
  }
  * { box-sizing: border-box; margin: 0; padding: 0; }
  html, body { width: 1200px; height: 800px; overflow: hidden; }
  body {
    background: var(--page-bg);
    font-family: "Montserrat", sans-serif;
    color: var(--ink);
    position: relative;
  }
  .flyer {
    position: absolute;
    left: 306px; top: 20px;
    width: 588px; height: 760px;
    background: var(--white);
    overflow: hidden;
    box-shadow: 0 6px 18px rgba(0,0,0,.18);
  }
  .flyer-art { position: absolute; inset: 0; }
  .figure {
    position: absolute;
    border-radius: 40% 40% 8px 8px;
    background: linear-gradient(180deg, #5b3f9e 0%, #7d4fae 55%, #c9c3e6 100%);
  }
  .figure-left { left: 2px; top: 97px; width: 155px; height: 291px; }
  .figure-right { left: 436px; top: 206px; width: 152px; height: 321px; background: linear-gradient(180deg, #5b3f9e 0%, #c9c3e6 60%, #4f4f9a 100%); }

  .bubble { position: absolute; font-weight: 700; line-height: 1.25; }
  .bubble-question {
    left: 76px; top: 25px; width: 216px; height: 53px;
    background: var(--lime);
    padding: 10px 10px;
    font-size: 12.4px; font-weight: 800;
    line-height: 1.1;
    text-transform: uppercase; letter-spacing: .01em;
  }
  .bubble-stop {
    left: 293px; top: 96px; width: 140px; height: 39px;
    background: var(--sky);
    display: flex; align-items: center; justify-content: center;
    font-size: 15.2px; font-weight: 800;
  }
  .bubble-advice {
    left: 206px; top: 148px; width: 256px; height: 76px;
    background: var(--sky);
    padding: 7px 10px 0 14px;
    font-size: 12.2px; font-weight: 600;
    line-height: 1.3;
  }
  .bubble-fact {
    left: 163px; top: 250px; width: 265px; height: 129px;
    background: var(--sky);
    padding: 11px 6px 0 16px;
    font-size: 12.4px; font-weight: 600;
    line-height: 1.2;
  }
  .bubble-fact cite {
    display: block; text-align: right;
    font-style: normal; color: var(--white);
    margin-top: 4px;
  }

  .brand {
    position: absolute;
    left: 462px; top: 30px; width: 116px;
    text-align: center;
    font-size: 13px; font-weight: 700; line-height: 1.2;
    color: var(--ink);
  }

  .section-label {
    position: absolute;
    left: 0; top: 472px; width: 262px; height: 34px;
    background: var(--label-blue);
    border-radius: 0 17px 17px 0;
    color: var(--white);
    font-size: 17px; font-weight: 800;
    display: flex; align-items: center;
    padding-left: 7px;
  }
  .risk-list {
    position: absolute;
    left: 26px; top: 536px; width: 556px;
    list-style: none;
    font-size: 17px; font-weight: 500; line-height: 20px;
  }
  .risk-list li { position: relative; }
  .risk-list li::before {
    content: ""; position: absolute;
    left: -13px; top: 6px;
    width: 8px; height: 8px; border-radius: 50%;
    background: var(--bullet-blue);
  }
  .risk-list li + li { margin-top: 22px; }
  .cta {
    position: absolute;
    left: 134px; top: 705px; width: 320px; height: 38px;
    background: var(--label-blue);
    border-radius: 19px;
    color: var(--white);
    font-size: 17.5px; font-weight: 800;
    display: flex; align-items: center; justify-content: center;
  }
</style>
</head>
<body>
  <main class="flyer">
    <svg class="flyer-art" width="588" height="760" viewBox="0 0 588 760" aria-hidden="true">
      <path d="M0 0 H588 V535 C 480 532, 360 512, 280 480 C 200 440, 120 383, 0 385 Z" fill="var(--flyer-blue)"/>
      <path d="M588 535 C 480 532, 360 512, 280 480 C 200 440, 120 383, 0 385" fill="none" stroke="var(--maroon)" stroke-width="3"/>
      <path d="M452 0 H588 V82 C 545 116, 468 112, 452 50 Z" fill="var(--white)"/>
      <polygon points="113,94 160,79 134,79" fill="var(--lime)"/>
      <polygon points="382,135 408,147 400,135" fill="var(--sky)"/>
      <polygon points="369,224 418,246 405,224" fill="var(--sky)"/>
      <polygon points="329,379 382,418 369,379" fill="var(--sky)"/>
    </svg>

    <div class="figure figure-left" role="img" aria-label="Illustration of a teen seen from behind, texting on a phone"></div>
    <div class="figure figure-right" role="img" aria-label="Illustration of a second teen seen from behind, reading a phone"></div>

    <p class="brand">Lowfield Care</p>

    <p class="bubble bubble-question">I'm thinking about using<br>drugs and alcohol.</p>
    <p class="bubble bubble-stop">JUST SAY NO!</p>
    <p class="bubble bubble-advice">Talk to your parents, your<br>teachers at school, or your doctor<br>about how drugs and alcohol can<br>harm you.</p>
    <div class="bubble bubble-fact">
      <p>Did you know that alcohol and drugs<br>could lead to - The development of<br>chronic diseases and other serious<br>problems including: High blood<br>pressure, heart disease, stroke, liver<br>disease, and digestive problems.</p>
      <cite>-rmqhealthnet.org</cite>
    </div>

    <h2 class="section-label">RISKS OF SUBSTANCE USE</h2>
    <ul class="risk-list">
      <li>Affect the growth and development of teens,<br>especially brain development.</li>
      <li>Occur more frequently with other risky behaviors.</li>
      <li>If you use drugs and alcohol at an early age,<br>it increases your chances of becoming addicted later in life.</li>
    </ul>

    <p class="cta">Say No to Drugs and Alcohol!</p>
  </main>
</body>
</html>
```